Advertisement flyer for fire sprinkler repair parts. The projected audience are contractors.

I need a flyer advertising specific parts that we are stocking at our company "Coastal Valveline Supply." I have attached a picture of our logo. I want the title to say "Fire Pump Repair Parts and Accessories." I want to specifically advertise the following parts: Repack Kits and Repair Parts, Jockey Pumps, Pump Controllers, Casing Relief Valves, Air Release Valves, Suction/Discharge Gauges, Pump Shaft Couplers & Shim Kits, Fire Pump Relief Valves, and UL Listed Pressure Reducing Valves. I have attached pictures of the manufacturers I want to advertise on this flyer. I have also attached pictures of some of the parts we are stocking that I would like to be included somewhere in the flyer. I would like all of the pictures to have a transparent background. Also I would like our phone number :(800)-318-4027, and our website www.valvelinesupply-demo.com included. I made my own design that I have Attached. You do not have to go based off this design, but I would like the basic content to be the same. We do have Same- Day shipping as well as Free Tech Support if you can include that anywhere.

```html
<!DOCTYPE html>
<html lang="en">
<head>
<meta charset="utf-8">
<title>Fire Pump Repair Parts &amp; Accessories — Coastal Valveline Supply</title>
<link rel="stylesheet" href="https://fonts.googleapis.com/css2?family=Roboto+Slab:wght@800&family=Oswald:wght@500;600&family=Roboto:wght@400;700&display=swap">
<style>
  :root {
    --red: #c4161c;
    --red-deep: #a10f14;
    --red-light: #d8343a;
    --white: #ffffff;
    --gold: #c9a66b;
    --blue: #2a4d9b;
    --backdrop: #ececec;
    --divider: #9a9a9a;
  }
  * { margin: 0; padding: 0; box-sizing: border-box; }
  html, body { width: 1080px; height: 1200px; overflow: hidden; }
  body { background: var(--backdrop); font-family: "Roboto", Arial, sans-serif; }

  .flyer {
    position: absolute; left: 137px; top: 30px;
    width: 806px; height: 1140px;
    background: var(--white); overflow: hidden;
    box-shadow: 0 4px 18px rgba(0,0,0,.18);
  }

  .flyer-header {
    position: absolute; left: 0; top: 0; width: 806px; height: 219px;
    background: linear-gradient(100deg, var(--red-deep) 0%, var(--red) 45%, var(--red-light) 75%, var(--red) 100%);
    display: flex; align-items: center; justify-content: center;
  }
  .flyer-title {
    font-family: "Roboto Slab", Georgia, serif; font-weight: 800;
    color: var(--white); font-size: 59px; line-height: 68px; text-align: center;
    letter-spacing: .5px; text-shadow: 0 2px 4px rgba(0,0,0,.25);
  }

  .hero { position: absolute; left: 0; top: 219px; width: 806px; height: 583px; }
  .hero-photo {
    position: absolute; inset: 0;
    background: linear-gradient(160deg, #d9d4d0 0%, #b8aaa5 30%, #b0392f 55%, #8f2620 75%, #c9c3bf 100%);
  }
  .parts-list { position: absolute; left: 50px; top: 48px; list-style: none; }
  .parts-list li {
    position: relative; padding-left: 32px;
    font-family: "Oswald", "Arial Narrow", sans-serif; font-weight: 600;
    font-size: 26px; line-height: 50px; text-transform: uppercase; color: var(--white);
    text-shadow: -2px -2px 0 var(--red), 2px -2px 0 var(--red), -2px 2px 0 var(--red), 2px 2px 0 var(--red), 0 3px 4px rgba(0,0,0,.4);
  }
  .parts-list li::before {
    content: ""; position: absolute; left: 0; top: 17px; width: 16px; height: 16px;
    border-radius: 50%; background: var(--white); border: 4px solid var(--red);
  }

  .product-panel {
    position: absolute; left: 562px; top: 0; width: 244px; height: 583px;
    background: rgba(255,255,255,.55);
  }
  .product-shot { position: absolute; border-radius: 6px; }
  .shot-booster { left: 34px; top: 24px; width: 60px; height: 162px; background: linear-gradient(180deg, #e6dcc0, #9fb4c8); }
  .shot-prv { left: 112px; top: 30px; width: 100px; height: 150px; background: linear-gradient(180deg, #c7a36a, #a88546); }
  .shot-pumpset { left: 24px; top: 235px; width: 115px; height: 60px; background: linear-gradient(180deg, #d2352f, #9c1d19); }
  .shot-controller { left: 150px; top: 200px; width: 70px; height: 120px; background: linear-gradient(180deg, #d2352f, #9c1d19); }
  .shot-kit { left: 28px; top: 350px; width: 150px; height: 100px; background: linear-gradient(180deg, #c9c5c2, #a8a39f); border-radius: 14px; }

  .delivery-badge {
    position: absolute; left: 32px; top: 478px; width: 66px; height: 66px;
    border: 3px solid var(--red); border-radius: 50%;
    display: flex; flex-direction: column; align-items: center; justify-content: center;
    font-family: "Oswald", sans-serif; font-weight: 600; color: var(--red);
    font-size: 11px; line-height: 12px; text-align: center;
  }
  .support-dot {
    position: absolute; left: 118px; top: 478px; width: 66px; height: 66px;
    border-radius: 50%; background: var(--red);
  }

  .footer { position: absolute; left: 0; top: 802px; width: 806px; height: 338px; }
  .swoosh { position: absolute; left: 0; top: 0; }

  .maker-grid {
    position: absolute; left: 36px; top: 34px; width: 446px;
    display: grid; grid-template-columns: repeat(4, auto); justify-content: space-between;
    row-gap: 30px; column-gap: 12px;
    font-family: "Oswald", sans-serif; font-weight: 600; color: var(--red-deep);
    text-transform: uppercase; font-size: 14px; line-height: 20px;
  }
  .maker { white-space: nowrap; }

  .client-mark { position: absolute; left: 40px; top: 150px; display: flex; align-items: center; gap: 14px; }
  .client-square { width: 44px; height: 44px; background: var(--red); }
  .client-name { font-family: "Roboto", Arial, sans-serif; font-weight: 400; color: var(--blue); font-size: 30px; line-height: 34px; }

  .footer-divider { position: absolute; left: 500px; top: 26px; width: 2px; height: 130px; background: var(--divider); }
  .service-block {
    position: absolute; left: 516px; top: 30px; width: 276px; text-align: center;
    font-family: "Oswald", sans-serif; font-weight: 500; color: var(--red);
    font-size: 21px; line-height: 26px; text-transform: uppercase;
  }
  .social-row { display: flex; gap: 6px; justify-content: center; margin-top: 6px; }
  .social-dot { width: 22px; height: 22px; border-radius: 50%; background: var(--red); }

  .contact { position: absolute; right: 34px; top: 246px; text-align: right; color: var(--white); }
  .contact-phone { font-family: "Roboto", Arial, sans-serif; font-weight: 700; font-size: 40px; line-height: 46px; }
  .contact-web { font-family: "Roboto", Arial, sans-serif; font-weight: 400; font-size: 24px; line-height: 32px; text-transform: uppercase; }
</style>
</head>
<body>
  <main class="flyer">
    <header class="flyer-header">
      <h1 class="flyer-title">Fire Pump Repair<br>Parts &amp; Accessories</h1>
    </header>

    <section class="hero">
      <div class="hero-photo" role="img" aria-label="Fire pump room with red pumps, valves and piping"></div>
      <ul class="parts-list">
        <li>Repack kits &amp; repair parts,</li>
        <li>Jockey pumps,</li>
        <li>Pump controllers,</li>
        <li>Casing relief valves,</li>
        <li>Air release valves,</li>
        <li>Suction/discharge gauges,</li>
        <li>Pump shaft couplers &amp; shim kits,</li>
        <li>Fire pump relief valves</li>
        <li>&amp; UL listed pressure reducing valves.</li>
      </ul>
      <aside class="product-panel">
        <div class="product-shot shot-booster" role="img" aria-label="Vertical multistage jockey pump"></div>
        <div class="product-shot shot-prv" role="img" aria-label="Bronze pressure reducing valve"></div>
        <div class="product-shot shot-pumpset" role="img" aria-label="Red horizontal fire pump set"></div>
        <div class="product-shot shot-controller" role="img" aria-label="Red fire pump relief valve"></div>
        <div class="product-shot shot-kit" role="img" aria-label="Pump repack kit with gaskets and hardware"></div>
        <div class="delivery-badge"><span>SAME DAY</span><span>DELIVERY</span></div>
        <div class="support-dot" aria-hidden="true"></div>
      </aside>
    </section>

    <footer class="footer">
      <svg class="swoosh" width="806" height="338" viewBox="0 0 806 338" aria-hidden="true">
        <path d="M0 310 C 250 300 480 190 806 130 L806 338 L0 338 Z" fill="var(--red)"/>
        <path d="M0 304 C 250 294 480 184 806 124" fill="none" stroke="var(--gold)" stroke-width="5"/>
      </svg>

      <div class="maker-grid">
        <span class="maker">Crestline Fire Pump</span>
        <span class="maker">Norvale Pumps</span>
        <span class="maker">Halden Pump Co.</span>
        <span class="maker">Verant Valve</span>
        <span class="maker">Brookfield Pump</span>
        <span class="maker">Solano Water</span>
        <span class="maker">Tidewell</span>
        <span class="maker">Marston Rowe</span>
      </div>

      <div class="client-mark">
        <span class="client-square" aria-hidden="true"></span>
        <span class="client-name">Coastal Valveline Supply</span>
      </div>

      <div class="footer-divider"></div>
      <div class="service-block">
        <p>Same- Day Shipping</p>
        <p>Free Tech Support</p>
        <div class="social-row" aria-hidden="true">
          <span class="social-dot"></span><span class="social-dot"></span><span class="social-dot"></span><span class="social-dot"></span><span class="social-dot"></span>
        </div>
      </div>

      <div class="contact">
        <p class="contact-phone">(800)-318-4027</p>
        <p class="contact-web">valvelinesupply-demo.com</p>
      </div>
    </footer>
  </main>
</body>
</html>
```